Small Business Broker Business Card Design

A business card design for a small business brokerage, which is a financial service, not unlike real estate brokerage, but for small businesses such as laundromats, pizza shops, restaurants, cleaners etc. The designs should all be simple, more conservative in nature, using the colors and font of the logo. Again, think real estate Brokerage as a business context
Contact Information for Business Card
Name: Glen R. Harlow. Title: Small Business Advisor. Email: g.harlow@bayfieldcapitalworks.example. Mobile: (555) 274-3918. Office: (555) 806-2147. www.bayfieldcapitalworks.example

```html
<!DOCTYPE html>
<html lang="en">
<head>
<meta charset="utf-8">
<title>Bayfield Capital Works — Business Card</title>
<link rel="stylesheet" href="https://fonts.googleapis.com/css2?family=League+Spartan:wght@600&family=Montserrat:wght@400;500;700&display=swap">
<style>
  :root {
    --navy: #1c3768;
    --navy-deep: #19315e;
    --green: #8cc63f;
    --ink: #1a1a1a;
    --paper: #ffffff;
    --backdrop: #9a9a9a;
  }
  * { margin: 0; padding: 0; box-sizing: border-box; }
  html, body { width: 1093px; height: 1200px; overflow: hidden; }
  body {
    background: var(--backdrop);
    font-family: "Montserrat", Arial, sans-serif;
    position: relative;
  }
  .card {
    position: absolute;
    left: 265px;
    width: 581px;
    height: 364px;
    border-radius: 24px;
    overflow: hidden;
  }
  .card--front { top: 225px; background: var(--paper); }
  .card--back { top: 615px; background: var(--navy); }

  /* front */
  .mark-square {
    position: absolute;
    left: 82px; top: 98px;
    width: 120px; height: 120px;
    background: var(--navy);
  }
  .divider {
    position: absolute;
    left: 257px; top: 74px;
    width: 1.5px; height: 163px;
    background: var(--navy);
  }
  .person { position: absolute; left: 270px; top: 74px; }
  .person__name {
    font-weight: 700;
    font-size: 22px;
    color: var(--navy);
    line-height: 1.1;
  }
  .person__title {
    font-size: 13px;
    color: var(--ink);
    margin-top: 2px;
  }
  .contacts {
    position: absolute;
    left: 273px; top: 158px;
    list-style: none;
  }
  .contacts li {
    display: flex;
    align-items: center;
    height: 20px;
    font-size: 12.6px;
    color: var(--ink);
  }
  .contacts li + li { margin-top: 0; }
  .contacts li:nth-child(2) { margin-top: 4px; }
  .contacts svg {
    width: 13px; height: 13px;
    margin-right: 9px;
    fill: var(--navy);
    flex: none;
  }
  .brand {
    position: absolute;
    left: 0; right: 0;
    text-align: center;
  }
  .brand__name {
    font-family: "League Spartan", "Montserrat", sans-serif;
    font-weight: 600;
    font-size: 28px;
    line-height: 1;
    letter-spacing: 0.3px;
  }
  .brand__tagline {
    font-family: "Montserrat", Arial, sans-serif;
    font-weight: 700;
    color: var(--green);
    text-transform: uppercase;
  }
  .card--front .brand { top: 298px; }
  .card--front .brand__name { color: var(--navy); }
  .card--front .brand__tagline { font-size: 11.6px; letter-spacing: 2.4px; margin-top: 3px; }

  /* back */
  .back-texture {
    position: absolute; inset: 0;
    background: radial-gradient(ellipse at 100% 0%, rgba(140,165,215,0.35) 0%, rgba(28,55,104,0) 55%), var(--navy-deep);
  }
  .card--back .brand { top: 268px; }
  .card--back .brand__name { color: var(--paper); font-size: 20.5px; }
  .card--back .brand__tagline { font-size: 9.4px; letter-spacing: 1.8px; margin-top: 3px; }
</style>
</head>
<body>

<section class="card card--front" aria-label="Business card front">
  <div class="mark-square" aria-hidden="true"></div>
  <div class="divider"></div>

  <div class="person">
    <h1 class="person__name">Glen R. Harlow</h1>
    <p class="person__title">Small Business Advisor</p>
  </div>

  <ul class="contacts">
    <li>
      <svg viewBox="0 0 16 16" aria-hidden="true"><path d="M1 6c0-2 3-3.5 7-3.5S15 4 15 6v1.2h-3.4V5.6C10.5 5.2 5.5 5.2 4.4 5.6v1.6H1zM4 8h8l2 6H2z"/></svg>
      (555) 806-2147
    </li>
    <li>
      <svg viewBox="0 0 16 16" aria-hidden="true"><path d="M4 1.5l2 3.2-1.4 1.4c.8 1.8 2.4 3.4 4.2 4.2l1.4-1.4 3.2 2-.9 2.8C7 13.9 2.1 9 1.3 2.4z"/><path d="M9 1.5a5.5 5.5 0 0 1 5.5 5.5h-1.3A4.2 4.2 0 0 0 9 2.8zM9 4a3 3 0 0 1 3 3h-1.3A1.7 1.7 0 0 0 9 5.3z"/></svg>
      (555) 274-3918
    </li>
    <li>
      <svg viewBox="0 0 16 16" aria-hidden="true"><path d="M1 3.5h14v1.2L8 9 1 4.7zM1 6.2l7 4.3 7-4.3v6.3H1z"/></svg>
      g.harlow@bayfieldcapitalworks.example
    </li>
    <li>
      <svg viewBox="0 0 16 16" aria-hidden="true"><circle cx="8" cy="8" r="7"/><path d="M4 4.5l2.5.5 1 2-2 1.5.5 3L4 10 3 7zM9.5 3l2.5 1.5.5 3-2 .5-1-2z" fill="#fff"/></svg>
      www.bayfieldcapitalworks.example
    </li>
  </ul>

  <div class="brand">
    <p class="brand__name">BAYFIELD CAPITAL WORKS, INC</p>
    <p class="brand__tagline">Confidently buy or sell a local business today</p>
  </div>
</section>

<section class="card card--back" aria-label="Business card back">
  <div class="back-texture" role="img" aria-label="Faint repeating brand-mark background pattern in navy tones"></div>
  <div class="brand">
    <p class="brand__name">BAYFIELD CAPITAL WORKS, INC</p>
    <p class="brand__tagline">Confidently buy or sell a local business today</p>
  </div>
</section>

</body>
</html>
```